Homepage layout for online ad network

Attached is our Valtro Media logo and updated brief (I can't seem to delete the old logo and brief, but they're no longer relevant).

This project was originally posted with a different logo and corporate name, but we have decided to stay with our current logo and name and redesign the site.

Your design is for a homepage only - design, no coding (I'll get someone else to take your PSD and code it).

Your homepage will make use of a Flash slider - BUT YOU ARE NOT REQUIRED TO PROVIDE THE FLASH. Instead, simply provide the layout and at least two static examples out of the four different sections that will eventually be in the slider.

Much of this design is based on the design of a competitor (listed in the brief).

Please ask whatever questions you need to in order to clarify instructions.
Updates

Project updated to include new logo (and correspondingly new color scheme).

Brief changed slightly.

Thank you for submitting designs for this project in the past.

After some internal strategy work, we have decided to retain our initial corporate identity, Valtro Media.

If you have submitted a design for the original brief and are available, please re-work your best prior design to reflect the color scheme in the newly uploaded logo.

Target Market(s)

This site is aimed primarily at young professionals who buy digital media on behalf of large advertisers.

Industry/Entity Type

Media

Requirements
Must have
• modern white space
Should not have
• no Flash outside of slider

```html
<!DOCTYPE html>
<html lang="en">
<head>
<meta charset="utf-8">
<title>Valtro Media</title>
<link rel="stylesheet" href="https://fonts.googleapis.com/css2?family=Montserrat:wght@400;500;600;700&family=Arimo:wght@400;700&family=Roboto+Condensed:wght@300;400;700&display=swap">
<style>
  :root {
    --lime: #d4df24;
    --lime-light: #eef45a;
    --red: #c01f30;
    --ink: #231f20;
    --text: #2b2b2b;
    --rule: #6d6d6d;
    --band: #d2d2d2;
    --white: #ffffff;
  }
  * { margin: 0; padding: 0; box-sizing: border-box; }
  html, body { width: 1200px; height: 1000px; overflow: hidden; background: var(--white); }
  body { position: relative; font-family: "Arimo", Arial, sans-serif; color: var(--text); }

  .site-header { position: absolute; left: 0; top: 0; width: 1200px; height: 116px; border-bottom: 4px solid var(--lime); }
  .brand { position: absolute; left: 134px; top: 34px; display: flex; align-items: center; gap: 12px; }
  .brand-mark { width: 30px; height: 30px; background: var(--lime); }
  .brand-name { font-family: "Montserrat", sans-serif; font-weight: 500; font-size: 34px; color: var(--ink); letter-spacing: -0.5px; }
  .brand-pointer { position: absolute; left: 253px; top: 101px; width: 0; height: 0; border-left: 8px solid transparent; border-right: 8px solid transparent; border-bottom: 12px solid var(--lime); }
  .tagline { position: absolute; right: 117px; top: 25px; font-family: "Montserrat", sans-serif; font-weight: 600; font-size: 12px; color: var(--red); letter-spacing: 0.2px; }
  .main-nav { position: absolute; right: 117px; top: 68px; display: flex; height: 33px; }
  .main-nav a { font-family: "Montserrat", sans-serif; font-weight: 700; font-size: 12.5px; color: var(--ink); text-decoration: none; padding: 10px 14px 0; border-left: 1px solid #cfcfcf; letter-spacing: 0.3px; }
  .main-nav a:first-child { border-left: none; }
  .main-nav a.is-active { border-right: 1px solid var(--lime); }
  .main-nav a:last-child { padding-right: 0; }

  .hero-band { position: absolute; left: 0; top: 120px; width: 1200px; height: 220px; background: linear-gradient(var(--band), var(--white)); }

  .slider { position: absolute; left: 123px; top: 150px; width: 960px; height: 351px; background: linear-gradient(90deg, #dfe3e8 0%, #ffffff 30%, #f2f4f7 60%, #e4e9f0 100%); box-shadow: 0 6px 8px rgba(0,0,0,0.45); overflow: hidden; }
  .slide-photo { position: absolute; left: 500px; top: 0; width: 460px; height: 351px; background: radial-gradient(ellipse at 45% 55%, #d8a98a 0%, #b98168 30%, #5a3a2c 55%, #e8edf3 80%); }
  .slide-title { position: absolute; left: 104px; top: 120px; font-family: "Montserrat", sans-serif; font-weight: 700; font-size: 41px; color: var(--ink); letter-spacing: 0.5px; line-height: 1; }
  .slide-sub { position: absolute; left: 105px; top: 166px; font-family: "Montserrat", sans-serif; font-weight: 500; font-size: 21px; line-height: 24px; color: var(--red); letter-spacing: 0.5px; }
  .slide-arrow { position: absolute; top: 158px; }
  .slide-arrow.prev { left: 18px; }
  .slide-arrow.next { right: 18px; }

  .slider-dots { position: absolute; left: 526px; top: 516px; display: flex; gap: 13px; }
  .slider-dots span { width: 15px; height: 15px; border-radius: 50%; background: var(--ink); }
  .slider-dots span.is-current { background: var(--lime); }

  .about { position: absolute; left: 122px; top: 555px; width: 580px; }
  .about-heading { display: flex; align-items: flex-end; gap: 10px; font-family: "Roboto Condensed", sans-serif; font-size: 25px; font-weight: 300; color: var(--ink); letter-spacing: 0.3px; }
  .about-heading .mark { width: 26px; height: 26px; background: var(--lime); margin-bottom: 4px; }
  .about-heading strong { font-weight: 400; }
  .about-lead { margin-top: 14px; font-size: 18px; line-height: 24px; color: var(--red); }
  .about-body { margin-top: 12px; font-size: 14px; line-height: 24.5px; color: var(--text); width: 540px; }

  .footer-links { position: absolute; left: 122px; top: 835px; width: 576px; border-top: 1px solid var(--rule); }
  .footer-links ul { list-style: none; display: flex; padding-top: 19px; margin-left: -2px; }
  .footer-links li { font-family: "Montserrat", sans-serif; font-weight: 500; font-size: 13px; color: var(--ink); margin-right: 22px; white-space: nowrap; letter-spacing: 0.3px; }
  .footer-links li svg { vertical-align: -1px; margin-left: 4px; }

  .news { position: absolute; left: 728px; top: 540px; width: 355px; height: 350px; background: linear-gradient(90deg, rgba(0,0,0,0.06) 0, rgba(0,0,0,0) 14px); }
  .news-heading { position: absolute; left: 2px; top: 18px; width: 238px; height: 39px; background: linear-gradient(90deg, var(--lime) 0%, var(--lime-light) 40%, var(--lime) 100%); box-shadow: 1px 2px 4px rgba(0,0,0,0.35); font-family: "Roboto Condensed", sans-serif; font-size: 24px; color: var(--red); padding: 5px 0 0 31px; }
  .news-list { position: absolute; left: 39px; top: 75px; width: 300px; list-style: none; }
  .news-list li { margin-bottom: 18px; font-size: 12px; line-height: 16px; color: var(--text); }
  .news-date { display: block; font-weight: 700; color: var(--red); letter-spacing: 0.4px; }

  .copyright { position: absolute; left: 122px; top: 898px; width: 959px; border-top: 1px solid var(--rule); text-align: center; padding-top: 17px; font-size: 12px; color: var(--text); }
</style>
</head>
<body>
  <header class="site-header">
    <div class="brand"><span class="brand-mark"></span><span class="brand-name">Valtro Media</span></div>
    <span class="brand-pointer"></span>
    <p class="tagline">SITE-SPECIFIC CAMPAIGNS AT RON PRICES</p>
    <nav class="main-nav">
      <a class="is-active" href="#">BEAUTY</a>
      <a href="#">COOKING</a>
      <a href="#">PARENTING</a>
      <a href="#">ENTERTAINMENT</a>
      <a href="#">VIDEO</a>
      <a href="#">CPC</a>
    </nav>
  </header>

  <div class="hero-band"></div>

  <section class="slider">
    <div class="slide-photo" role="img" aria-label="Beauty campaign photo: woman with yellow flowers in her hair"></div>
    <h2 class="slide-title">BEAUTY</h2>
    <p class="slide-sub">SITE SPECIFIC CAMPAIGNS<br>AT RON PRICES</p>
    <svg class="slide-arrow prev" width="32" height="50" viewBox="0 0 32 50"><path d="M28 2 L8 25 L28 48 L18 48 L0 25 L18 2 Z" fill="#231f20"/></svg>
    <svg class="slide-arrow next" width="32" height="50" viewBox="0 0 32 50"><path d="M4 2 L24 25 L4 48 L14 48 L32 25 L14 2 Z" fill="#231f20"/></svg>
  </section>

  <div class="slider-dots"><span class="is-current"></span><span></span><span></span><span></span><span></span><span></span></div>

  <section class="about">
    <h2 class="about-heading"><span class="mark"></span><span>ABOUT <strong>VALTRO MEDIA</strong></span></h2>
    <p class="about-lead">Lorem ipsum dolor sit amet, consectetur adipiscing elit. Mauris dignissim nulla pharetra risus iaculis at consequat turpis vulputate.</p>
    <p class="about-body">Sed scelerisque magna ut quam scelerisque dictum. Morbi purus quam, sodales id vehicula non, ultricies vitae justo. Vivamus sed augue ut elit dapibus adipiscing vel in elit. Mauris adipiscing, elit a laoreet eleifend, orci lacus condimentum enim, vitae venenatis enim velit ac dolor. Nullam augue mauris, tincidunt et bibendum nec, consequat ut dui. Sed id ante in purus vulputate adipiscing ac non justo. Nulla libero sem, venenatis in fringilla pulvinar, ornare ac diam.</p>
  </section>

  <nav class="footer-links">
    <ul>
      <li>ABOUT US<svg width="12" height="11" viewBox="0 0 12 11"><path d="M0 5.5 H10 M6 1 L10.5 5.5 L6 10" stroke="#c01f30" stroke-width="2" fill="none"/></svg></li>
      <li>CONTACT US<svg width="12" height="11" viewBox="0 0 12 11"><path d="M0 5.5 H10 M6 1 L10.5 5.5 L6 10" stroke="#c01f30" stroke-width="2" fill="none"/></svg></li>
      <li>MANAGEMENT TEAM<svg width="12" height="11" viewBox="0 0 12 11"><path d="M0 5.5 H10 M6 1 L10.5 5.5 L6 10" stroke="#c01f30" stroke-width="2" fill="none"/></svg></li>
      <li>NEWS<svg width="12" height="11" viewBox="0 0 12 11"><path d="M0 5.5 H10 M6 1 L10.5 5.5 L6 10" stroke="#c01f30" stroke-width="2" fill="none"/></svg></li>
      <li>CAREERS<svg width="12" height="11" viewBox="0 0 12 11"><path d="M0 5.5 H10 M6 1 L10.5 5.5 L6 10" stroke="#c01f30" stroke-width="2" fill="none"/></svg></li>
    </ul>
  </nav>

  <aside class="news">
    <h2 class="news-heading">VALTRO NEWS</h2>
    <ul class="news-list">
      <li><span class="news-date">JANUARY 15, 2011</span>Valtro Media unveils new web site design and digital strategy</li>
      <li><span class="news-date">DECEMBER 22, 2010</span>Valtro Media featured in Foundermag.com as one<br>of the fastest grown online ad agencies.</li>
      <li><span class="news-date">NOVEMBER 15, 2010</span>As RTB Goes Mainstream, Display Services Try To<br>Pull Publishers Along</li>
      <li><span class="news-date">NOVEMBER 9, 2010</span>Morbi purus quam, sodales id vehicula non, ultricies vitae justo</li>
    </ul>
  </aside>

  <footer class="copyright">Copyright 2011 Valtro Media. All Rights Reserved</footer>
</body>
</html>
```